Corporate Design - Immobilienverwaltungsgesellschaft
Zielgruppe
An- und Verkauf, Verwaltung und Vermietung von Immobilien
Zielgruppen: Immobilienspekulanten, Wohnungskäufer, Mieter, Vermieter
Aufgabenstellung
Wir suchen ein hochwertiges Design für eine in Gründung befindliche Gesellschaft mit beschränkter Haftung.
Diese wird aus 2 Gesellschaftern, Katrin und Torsten Fellmer bestehen.
Das Hauptziel der Gesellschaft wird der An- und Verkauf von Immobilien bis zu 1. Million Euro je Kaufobjekt sein
Mit dem Nachnamen der Gesellschafter kann auch gespielt werden, beispielsweise bei Abkürzungen. Die Bezeichnung F&F Verwaltungsgesellschaft mbH ist nicht zwingend, lediglich das Kürzel 'mbH' oder auch 'GmbH' ist aufgrund der Rechtsform der Gesellschaft zwingend aufzunehmen.
Diverse Designideen haben wir bereits vorliegen; hierauf kann aufgebaut werden, siehe Uploads
Unter anderem eine Anlehnung an die unter derselben Firmenadresse der Gesellschaft bestehende Rechtsanwaltskanzlei und deren Cooperate Design wäre eine Idee, jedoch keine zwingende Voraussetzung.

```html
<!DOCTYPE html>
<html lang="de">
<head>
<meta charset="utf-8">
<title>F&amp;F Verwaltungsgesellschaft mbH – Corporate Design</title>
<link rel="stylesheet" href="https://fonts.googleapis.com/css2?family=Source+Sans+3:wght@400;600&display=swap">
<style>
:root{
  --blue:#1a7cc1;
  --blue-deep:#0d5fa3;
  --blue-light:#4a9bd6;
  --navy:#1e4f8c;
  --ink:#333333;
  --grey-stage:#76766f;
  --paper:#ffffff;
  --paper-soft:#eeeeec;
  --mock-bg:#e6e6e6;
  --watermark:#ececec;
}
*{box-sizing:border-box;margin:0;padding:0}
html,body{width:1200px;height:4000px;overflow:hidden}
body{font-family:"Source Sans 3",sans-serif;color:var(--ink);background:var(--paper);position:relative}
.sprite{position:absolute;width:0;height:0}

/* brand lockup */
.brand{display:flex;align-items:center;gap:22px}
.brand-ring{border-radius:50%;border:6px solid var(--blue);flex:none}
.brand-name{font-weight:600;color:var(--blue);line-height:1.15}

/* intro */
.intro{position:absolute;left:0;top:0;width:1200px;height:476px;display:flex;align-items:center;justify-content:center}
.intro .brand-ring{width:180px;height:180px}
.intro .brand-name{font-size:24px;max-width:310px}

.stage{position:absolute;left:0;top:476px;width:1200px;height:3280px;background:var(--grey-stage)}

.paper-panel{position:absolute;left:216px;top:61px;width:768px;height:473px;background:var(--paper-soft);display:flex;align-items:center;justify-content:center}
.paper-panel .brand-ring{width:170px;height:170px}
.paper-panel .brand-name{font-size:24px;max-width:310px}

/* business cards */
.card{position:absolute;width:425px;height:275px;box-shadow:0 8px 18px rgba(0,0,0,.35);overflow:hidden}
.card-front{background:var(--paper);border-bottom:11px solid var(--blue)}
.card-front .brand{position:absolute;left:26px;top:16px;gap:12px}
.card-front .brand-ring{width:115px;height:115px;border-width:5px}
.card-front .brand-name{font-size:14px;max-width:185px}
.card-person{position:absolute;left:32px;top:150px;font-size:15px;line-height:1.3}
.card-person .name{color:var(--blue);font-weight:600}
.card-contacts{position:absolute;left:274px;top:140px;list-style:none;font-size:14px;line-height:19px}
.card-address{position:absolute;left:32px;top:234px;font-size:13px}
.card-back{background:linear-gradient(135deg,var(--blue-light),var(--blue-deep));display:flex;flex-direction:column;align-items:center;justify-content:flex-start;padding-top:42px;gap:20px}
.card-back .brand-ring{width:177px;height:177px;border:8px solid var(--navy);display:flex;align-items:center;justify-content:center}
.card-back .mark{font-weight:600;font-size:44px;color:var(--navy)}
.card-back .url{font-weight:600;font-size:16px;color:var(--navy)}
.card-row .card-front{left:126px;top:595px}
.card-row .card-back{left:635px;top:595px}

.mock-panel{position:absolute;left:166px;top:930px;width:866px;height:754px;background:var(--mock-bg)}
.mock-panel .card{transform:scale(.78);transform-origin:top left}
.mock-panel .card-back{left:70px;top:90px}
.mock-panel .card-front{left:440px;top:370px}

.contact-list li{display:flex;align-items:center;gap:9px}
.icon{width:13px;height:13px;fill:var(--blue);flex:none}

/* letterhead */
.letterhead{position:absolute;left:79px;top:1739px;width:1051px;height:1482px;background:var(--paper);overflow:hidden}
.letterhead .brand{position:absolute;left:585px;top:39px;gap:18px}
.letterhead .brand-ring{width:149px;height:149px}
.letterhead .brand-name{font-size:20px;max-width:250px}
.return-line{position:absolute;left:124px;top:226px;font-size:10.5px;padding-bottom:2px;border-bottom:1.5px solid var(--blue)}
.sender{position:absolute;left:795px;top:225px;border-left:2px solid var(--blue);padding-left:18px;font-size:15px;line-height:21px;height:231px}
.sender .name{color:var(--blue);font-weight:600}
.sender .gap{height:12px}
.sender .contact-list{list-style:none}
.fold-mark{position:absolute;left:0;height:1px;background:#9a9a9a}
.watermark{position:absolute;left:112px;top:985px;width:375px;height:375px;border-radius:50%;border:14px solid var(--watermark);display:flex;align-items:center;justify-content:center}
.watermark span{font-weight:600;font-size:100px;color:var(--watermark)}
.bank-line{position:absolute;left:110px;top:1420px;font-size:14px}
.bank-line b{font-weight:600}
.bank-line .sep{color:var(--blue)}
.letter-band{position:absolute;left:0;bottom:0;width:100%;height:22px;background:linear-gradient(90deg,var(--blue-deep),var(--blue-light) 60%,var(--blue))}

/* outro */
.outro{position:absolute;left:0;top:3756px;width:1200px;height:244px;background:linear-gradient(90deg,var(--blue-deep),#0a79b5 60%,#3a6d9e);display:flex;align-items:center;justify-content:center}
.outro .brand-ring{width:155px;height:155px;border-color:#ffffff}
.outro .brand-name{font-size:21px;color:#ffffff;max-width:270px}
</style>
</head>
<body>

<svg class="sprite" aria-hidden="true">
  <symbol id="ico-phone" viewBox="0 0 16 16"><path d="M3.6 1.2 6 3.6 4.7 5.5c.8 2 2.2 3.5 4.3 4.6l1.9-1.3 2.5 2.4-1.6 2.7C7 13.6 2.3 8.8 1 3z"/></symbol>
  <symbol id="ico-fax" viewBox="0 0 16 16"><path d="M4 1h8v4H4zM1 6h14v7h-3v2H4v-2H1zm4 5v3h6v-3zm7-3v1h2V8z"/></symbol>
  <symbol id="ico-mail" viewBox="0 0 16 16"><path d="M1 3h14v1L8 8.5 1 4zM1 5.6l7 4.4 7-4.4V13H1z"/></symbol>
  <symbol id="ico-web" viewBox="0 0 16 16"><path d="M8 1a7 7 0 1 0 0 14A7 7 0 0 0 8 1zm0 1.4c.8.9 1.4 2.2 1.6 3.6H6.4C6.6 4.6 7.2 3.3 8 2.4zM2.5 7h2.6a13 13 0 0 0 0 2H2.5a5.6 5.6 0 0 1 0-2zm4 0h3a11 11 0 0 1 0 2h-3a11 11 0 0 1 0-2zm4.4 0h2.6a5.6 5.6 0 0 1 0 2h-2.6a13 13 0 0 0 0-2zM6.4 10h3.2c-.2 1.4-.8 2.7-1.6 3.6-.8-.9-1.4-2.2-1.6-3.6z"/></symbol>
</svg>

<section class="intro">
  <div class="brand"><div class="brand-ring"></div><span class="brand-name">F&amp;F Verwaltungsgesellschaft mbH</span></div>
</section>

<section class="stage">
  <div class="paper-panel">
    <div class="brand"><div class="brand-ring"></div><span class="brand-name">F&amp;F Verwaltungsgesellschaft mbH</span></div>
  </div>

  <div class="card-row">
    <article class="card card-front">
      <div class="brand"><div class="brand-ring"></div><span class="brand-name">F&amp;F Verwaltungsgesellschaft mbH</span></div>
      <p class="card-person"><span class="name">Katrin Fellmer</span><br>Geschäftsführerin</p>
      <ul class="card-contacts contact-list">
        <li><svg class="icon"><use href="#ico-phone"/></svg>01234 / 567 890</li>
        <li><svg class="icon"><use href="#ico-fax"/></svg>01234 / 567 890</li>
        <li><svg class="icon"><use href="#ico-mail"/></svg>info@fundf-vg.de</li>
        <li><svg class="icon"><use href="#ico-web"/></svg>www.fundf-vg.de</li>
      </ul>
      <p class="card-address">Am Lindenhof 12 • 66111 Musterstadt</p>
    </article>
    <article class="card card-back">
      <div class="brand-ring"><span class="mark">F&amp;F</span></div>
      <p class="url">www.fundf-vg.de</p>
    </article>
  </div>

  <div class="mock-panel">
    <article class="card card-back">
      <div class="brand-ring"><span class="mark">F&amp;F</span></div>
      <p class="url">www.fundf-vg.de</p>
    </article>
    <article class="card card-front">
      <div class="brand"><div class="brand-ring"></div><span class="brand-name">F&amp;F Verwaltungsgesellschaft mbH</span></div>
      <p class="card-person"><span class="name">Katrin Fellmer</span><br>Geschäftsführerin</p>
      <ul class="card-contacts contact-list">
        <li><svg class="icon"><use href="#ico-phone"/></svg>01234 / 567 890</li>
        <li><svg class="icon"><use href="#ico-fax"/></svg>01234 / 567 890</li>
        <li><svg class="icon"><use href="#ico-mail"/></svg>info@fundf-vg.de</li>
        <li><svg class="icon"><use href="#ico-web"/></svg>www.fundf-vg.de</li>
      </ul>
      <p class="card-address">Am Lindenhof 12 • 66111 Musterstadt</p>
    </article>
  </div>

  <article class="letterhead">
    <div class="brand"><div class="brand-ring"></div><span class="brand-name">F&amp;F Verwaltungsgesellschaft mbH</span></div>
    <p class="return-line">F &amp; F Verwaltungsgesellschaft mbH • Am Lindenhof 12 • 66111 Musterstadt</p>
    <div class="sender">
      <p>Geschäftsführer:</p>
      <p class="name">Katrin Fellmer</p>
      <p class="name">Torsten Fellmer</p>
      <div class="gap"></div>
      <p>Am Lindenhof 12<br>66111 Musterstadt</p>
      <div class="gap"></div>
      <ul class="contact-list">
        <li><svg class="icon"><use href="#ico-phone"/></svg>01234 / 567 890</li>
        <li><svg class="icon"><use href="#ico-fax"/></svg>01234 / 567 890</li>
        <li><svg class="icon"><use href="#ico-mail"/></svg>info@fundf-vg.de</li>
        <li><svg class="icon"><use href="#ico-web"/></svg>www.fundf-vg.de</li>
      </ul>
      <div class="gap" style="height:6px"></div>
      <p>USt-IdNr. DE000111222</p>
    </div>
    <span class="fold-mark" style="top:539px;width:32px"></span>
    <span class="fold-mark" style="top:756px;width:50px"></span>
    <span class="fold-mark" style="top:1049px;width:32px"></span>
    <div class="watermark" aria-hidden="true"><span>F&amp;F</span></div>
    <p class="bank-line"><b>Bankverbindung:</b> Lindenbank Musterstadt <span class="sep">•</span> BIC: LINDDE12XXX • IBAN: DE00 1234 5678 9012 3456 78</p>
    <div class="letter-band"></div>
  </article>
</section>

<section class="outro">
  <div class="brand"><div class="brand-ring"></div><span class="brand-name">F&amp;F Verwaltungsgesellschaft mbH</span></div>
</section>

</body>
</html>
```